Industry / Entity Type

Financial consultancy / advisers

Current site is: http://www.brightmoor-counsel.com

Looking for a complete overhaul of this site, we are after a clean modern look. Will require the ability to easily add, update and remove content, hence the WordPress design.
Example:
Add case studies
Industry documentation (downloadable brochures / flyers and such)

What we like from our current site is the colour the fonts and the logo (the city of London) we would like to have other city outlines (NYC and Tokyo, Hong Kong, Singapore).

The site will be used by our potential clients to get in contact and re-view the case studies, if possible would like to have a client login area where they can download our documents like NDA’s etc and T&C’s.

Task Outline

Create a Web Design (Coded - Design and coding required)
Designer must provide full implementation/coding depending on the platform chosen by the client (i.e. WordPress theme, HTML/CSS, bootstrap etc.)

Task Description

I need a full website built that must work on desktop and mobile. I can provide the London city skyline and the font file, which we have used. Some stock industrial photos will be required.

Requirements:

*Splash page
*What We Do
*How We do it
*Who Are We? To have the same information and links as the current site
*Why use us?
*Clients: To have the same information and links as the current site
*Partners: To have the same information and links as the current site
*Contact:

Target Market(s)

Financial institutions trading Equities, Futures, Options, Forex and Fixed Income.
Regulators, Exchanges, ECN’s
Buy side firms and Sell side firms

Industry/Entity Type

Financial

Coding

Coded - Design and coding required

Number of Pages Required

5+ page

Font styles to use
Sans Serif

Colors
f04a50

Requirements
Must have
• Splash page
• What We Do
• How We do it
• Who Are We? To have the same information and links as the current site
• Why use us?
• Clients: To have the same information and links as the current site
• Partners: To have the same information and links as the current site
• Contact:

```html
<!DOCTYPE html>
<html lang="en">
<head>
<meta charset="utf-8">
<title>Brightmoor Counsel</title>
<link href="https://fonts.googleapis.com/css2?family=Maven+Pro:wght@400;500&family=Tenor+Sans&display=swap" rel="stylesheet">
<style>
:root{
  --red:#f04a50;
  --ink:#222222;
  --text:#666666;
  --muted:#8a8a8a;
  --panel:#f4f4f4;
  --line:#dddddd;
  --white:#ffffff;
  --night-top:#0e1d33;
  --night-bottom:#2c3a4c;
}
*{margin:0;padding:0;box-sizing:border-box}
html,body{width:1200px;height:2258px;overflow:hidden}
body{position:relative;background:var(--white);font-family:"Maven Pro",Arial,sans-serif;color:var(--text)}
.abs{position:absolute}
.display{font-family:"Tenor Sans","Maven Pro",sans-serif;font-variant:small-caps;color:var(--ink);letter-spacing:1px;font-weight:400}

/* hero */
.hero{left:0;top:0;width:1200px;height:550px}
.hero-photo{position:absolute;inset:0;background:linear-gradient(180deg,var(--night-top) 0%,#1d3350 40%,#5a5a52 62%,#3a3f44 75%,var(--night-bottom) 100%)}
.topbar{position:absolute;left:0;top:0;width:1200px;height:100px;border-bottom:1px solid rgba(255,255,255,.3)}
.brand{position:absolute;left:95px;top:36px;font-family:"Maven Pro",sans-serif;font-size:22px;font-weight:500;color:var(--white);letter-spacing:2px;text-transform:uppercase}
.nav{position:absolute;left:410px;top:40px;display:flex;gap:22px;list-style:none;font-size:15px;color:var(--white)}
.nav .active{color:var(--red)}
.nav svg{margin-top:2px}
.hero-title{position:absolute;left:0;width:1200px;top:195px;text-align:center;font-family:"Tenor Sans",sans-serif;font-size:42px;font-weight:400;color:var(--white);letter-spacing:1px}
.hero-sub{position:absolute;left:0;width:1200px;top:265px;text-align:center;font-size:20px;line-height:32px;color:var(--white);letter-spacing:.5px}
.hero-btn{position:absolute;left:487px;top:355px;width:226px;height:46px;border:2px solid var(--white);border-radius:23px;background:var(--red);color:var(--white);font-size:17px;font-weight:500;text-align:center;line-height:42px;letter-spacing:.5px}
.dots{position:absolute;left:565px;top:479px;display:flex;gap:5px}
.dots span{width:13px;height:13px;border:2px solid var(--white);border-radius:50%}
.dots .on{background:var(--white)}

/* welcome */
.welcome-title{left:0;width:1200px;top:600px;text-align:center;font-size:33px}
.welcome-text{left:230px;width:740px;top:656px;text-align:center;font-size:12.5px;line-height:25px}
.service{width:264px;text-align:center}
.icon-box{height:108px;display:flex;align-items:center;justify-content:center}
.service h3{margin-top:30px;font-size:20px;font-weight:500;color:var(--ink)}
.service p{margin-top:10px;font-size:12.5px;line-height:22px;color:var(--muted)}

/* how */
.how{left:0;top:1047px;width:1200px;height:413px;background:var(--panel);border-top:1px solid var(--line);border-bottom:1px solid var(--line)}
.how-photo{position:absolute;left:0;top:0;width:620px;height:413px;clip-path:polygon(0 0,100% 0,83.4% 100%,0 100%);background:radial-gradient(circle at 40% 45%,#c9a35a 0%,#6f6450 18%,#3e4a58 45%,#2a3340 100%)}
.section-title{font-size:31px}
.body-copy{font-size:12.5px;line-height:25px;color:var(--muted)}
.outline-btn{display:inline-block;border:1px solid #999;border-radius:17px;color:var(--red);font-size:12.5px;font-weight:500;text-align:center}

/* why */
.ticks{list-style:none;font-size:12.5px;color:var(--muted)}
.ticks li{display:flex;align-items:center;gap:10px;height:35px}
.laptop{left:630px;top:1535px;width:522px;height:310px}
.laptop-screen{position:absolute;left:50px;top:0;width:422px;height:285px;background:linear-gradient(180deg,#2a2a2a,#111);border-radius:14px 14px 0 0}
.laptop-display{position:absolute;left:64px;top:18px;width:394px;height:262px;background:linear-gradient(180deg,#e9ecf4,#ffffff)}
.laptop-base{position:absolute;left:0;top:285px;width:522px;height:18px;background:linear-gradient(180deg,#e2e2e2,#9a9a9a);border-radius:0 0 30px 30px}

/* footer */
.footer-rule{left:0;top:1904px;width:1200px;height:4px;background:var(--red)}
.footer-brand{left:77px;top:2025px;font-size:22px;font-weight:500;color:var(--ink);letter-spacing:2px;text-transform:uppercase}
.footer-title{font-size:19px}
.footer-links{list-style:none;font-size:12.5px;line-height:20px;color:var(--text)}
.email-field{left:590px;top:2060px;width:255px;height:32px;border-bottom:1px solid #bbb;font-size:12px;color:#aaa;padding:8px 0 0 12px}
.contact-row{display:flex;gap:16px;font-size:12.5px;line-height:21px;color:var(--text)}
.footer-divider{left:100px;top:2182px;width:1002px;height:1px;background:var(--line)}
.copyright{left:100px;top:2213px;font-size:12px;color:var(--text)}
.socials{left:977px;top:2210px;display:flex;gap:9px}
.socials span{width:24px;height:24px;border:1px solid var(--red);border-radius:50%}
</style>
</head>
<body>

<header class="abs hero">
  <div class="hero-photo" role="img" aria-label="Night photograph of a river bridge and city skyline lit up over the water"></div>
  <div class="topbar">
    <div class="brand">Brightmoor Counsel</div>
    <ul class="nav">
      <li class="active">Home</li><li>What we do</li><li>How we do it</li><li>Who are we</li><li>Why use us</li><li>Clients</li><li>Partners</li><li>Contact</li>
      <li><svg width="13" height="13" viewBox="0 0 13 13"><circle cx="5.5" cy="5.5" r="4" fill="none" stroke="#fff" stroke-width="2"/><line x1="8.5" y1="8.5" x2="12" y2="12" stroke="#fff" stroke-width="2"/></svg></li>
    </ul>
  </div>
  <h1 class="hero-title">BRIGHTMOOR COUNSEL</h1>
  <p class="hero-sub">Provide solutions to solve potential issues to get you the correct solution<br>at the correct price point to achieve the desired results</p>
  <div class="hero-btn">GET MORE INFO &gt;&gt;</div>
  <div class="dots"><span class="on"></span><span></span><span></span><span></span></div>
</header>

<section>
  <h2 class="abs display welcome-title">Welcome to Brightmoor Counsel</h2>
  <p class="abs welcome-text">Since founding Brightmoor Counsel in 2014 we have dedicated ourselves to the provision of services. What differentiates us from other advisers or consultancies is a genuine motivation to see our clients succeed.</p>

  <div class="abs service" style="left:72px;top:752px">
    <div class="icon-box"><svg width="112" height="108" viewBox="0 0 112 108">
      <rect x="40" y="2" width="68" height="96" fill="var(--red)"/>
      <rect x="56" y="20" width="40" height="5" fill="#fff"/><rect x="56" y="40" width="40" height="5" fill="#fff"/><rect x="56" y="60" width="40" height="5" fill="#fff"/><rect x="56" y="80" width="40" height="5" fill="#fff"/>
      <circle cx="22" cy="32" r="11" fill="var(--red)" stroke="#fff" stroke-width="3"/><circle cx="22" cy="32" r="4" fill="#fff"/>
      <g stroke="var(--red)" stroke-width="6"><line x1="30" y1="56" x2="30" y2="104"/><line x1="6" y1="80" x2="54" y2="80"/><line x1="13" y1="63" x2="47" y2="97"/><line x1="47" y1="63" x2="13" y2="97"/></g>
      <circle cx="30" cy="80" r="14" fill="var(--red)"/><circle cx="30" cy="80" r="6" fill="#fff"/>
    </svg></div>
    <h3>Data Management</h3>
    <p>At vero eos et accusamus et iustodi<br>dignissimos ducimus qui blan</p>
  </div>

  <div class="abs service" style="left:335px;top:752px">
    <div class="icon-box"><svg width="104" height="104" viewBox="0 0 104 104">
      <circle cx="52" cy="52" r="44" fill="none" stroke="var(--red)" stroke-width="14" stroke-dasharray="62 7"/>
      <rect x="30" y="58" width="11" height="20" fill="var(--red)"/><rect x="46" y="46" width="11" height="32" fill="var(--red)"/><rect x="62" y="34" width="11" height="44" fill="var(--red)"/>
    </svg></div>
    <h3>Analytics</h3>
    <p>At vero eos et accusamus et iustodi<br>dignissimos ducimus qui blan</p>
  </div>

  <div class="abs service" style="left:601px;top:752px">
    <div class="icon-box"><svg width="116" height="104" viewBox="0 0 116 104">
      <ellipse cx="44" cy="60" rx="40" ry="30" fill="var(--red)" stroke="#fff" stroke-width="4"/>
      <path d="M14 80 L6 100 L34 86Z" fill="var(--red)"/>
      <ellipse cx="66" cy="40" rx="46" ry="36" fill="var(--red)" stroke="#fff" stroke-width="4"/>
      <path d="M96 64 L108 88 L80 74Z" fill="var(--red)"/>
      <circle cx="46" cy="40" r="6" fill="#fff"/><circle cx="66" cy="40" r="6" fill="#fff"/><circle cx="86" cy="40" r="6" fill="#fff"/>
    </svg></div>
    <h3>Consulting</h3>
    <p>At vero eos et accusamus et iustodi<br>dignissimos ducimus qui blan</p>
  </div>

  <div class="abs service" style="left:863px;top:752px">
    <div class="icon-box"><svg width="104" height="104" viewBox="0 0 104 104">
      <circle cx="52" cy="52" r="30" fill="none" stroke="var(--red)" stroke-width="6"/>
      <ellipse cx="52" cy="52" rx="13" ry="30" fill="none" stroke="var(--red)" stroke-width="4"/>
      <line x1="22" y1="52" x2="82" y2="52" stroke="var(--red)" stroke-width="4"/>
      <line x1="27" y1="37" x2="77" y2="37" stroke="var(--red)" stroke-width="3"/><line x1="27" y1="67" x2="77" y2="67" stroke="var(--red)" stroke-width="3"/>
      <ellipse cx="52" cy="52" rx="50" ry="18" fill="none" stroke="var(--red)" stroke-width="6" transform="rotate(45 52 52)"/>
      <ellipse cx="52" cy="52" rx="50" ry="18" fill="none" stroke="var(--red)" stroke-width="6" transform="rotate(-45 52 52)"/>
    </svg></div>
    <h3>Trading</h3>
    <p>At vero eos et accusamus et iustodi<br>dignissimos ducimus qui blan</p>
  </div>
</section>

<section class="abs how">
  <div class="how-photo" role="img" aria-label="Glowing light bulb with gears inside against a chalkboard of formulas"></div>
  <h2 class="abs display section-title" style="left:665px;top:54px">How We Do It</h2>
  <p class="abs body-copy" style="left:665px;top:114px;width:445px">At vero eos et accusamus et iusto odio dignissimos ducimus qui blanditiis prasent ium voluptatum deleniti atque corrupti quo.</p>
  <p class="abs body-copy" style="left:665px;top:190px;width:445px">Dolores et quas molestias excepturi sint occaecati cupiditate non provident similiq ue sunt in culpa qui officia deserunt mollitia animi, id est laborum et dolorum fug t harum quidem rerum facilis est et expedita voluptas assumen est, omnis dolorr epellend poribus autem quibusdam et aut officiis.</p>
  <div class="abs outline-btn" style="left:665px;top:315px;width:132px;height:32px;line-height:30px">READ MORE &gt;&gt;</div>
</section>

<section>
  <h2 class="abs display section-title" style="left:100px;top:1538px">Why Choose us</h2>
  <ul class="abs ticks" style="left:98px;top:1594px">
    <li><svg width="15" height="15" viewBox="0 0 15 15"><circle cx="7.5" cy="7.5" r="7.5" fill="var(--red)"/><path d="M4 7.5l2.5 2.5 4.5-5" fill="none" stroke="#fff" stroke-width="2"/></svg>At vero eos et accusamus et iusto odio dignissimos ducimus qui blaniis</li>
    <li><svg width="15" height="15" viewBox="0 0 15 15"><circle cx="7.5" cy="7.5" r="7.5" fill="var(--red)"/><path d="M4 7.5l2.5 2.5 4.5-5" fill="none" stroke="#fff" stroke-width="2"/></svg>Praesentium voluptatum deleniti atque corrupti quos dolores et quas</li>
    <li><svg width="15" height="15" viewBox="0 0 15 15"><circle cx="7.5" cy="7.5" r="7.5" fill="var(--red)"/><path d="M4 7.5l2.5 2.5 4.5-5" fill="none" stroke="#fff" stroke-width="2"/></svg>Excepturi sint occaecati cupiditate non provident, similiqt in culpa qui</li>
    <li><svg width="15" height="15" viewBox="0 0 15 15"><circle cx="7.5" cy="7.5" r="7.5" fill="var(--red)"/><path d="M4 7.5l2.5 2.5 4.5-5" fill="none" stroke="#fff" stroke-width="2"/></svg>Nam libero tempore, cum soluta nobis est eligendi optio</li>
    <li><svg width="15" height="15" viewBox="0 0 15 15"><circle cx="7.5" cy="7.5" r="7.5" fill="var(--red)"/><path d="M4 7.5l2.5 2.5 4.5-5" fill="none" stroke="#fff" stroke-width="2"/></svg>Dit quo minus id quod maxime placeat facere possimus, omnis volup</li>
  </ul>
  <div class="abs outline-btn" style="left:100px;top:1800px;width:144px;height:35px;line-height:33px">READ MORE &gt;&gt;</div>
  <div class="abs laptop" role="img" aria-label="Laptop showing a candlestick trading chart">
    <div class="laptop-screen"></div>
    <div class="laptop-display"></div>
    <div class="laptop-base"></div>
  </div>
</section>

<footer>
  <div class="abs footer-rule"></div>
  <div class="abs footer-brand">Brightmoor Counsel</div>

  <h4 class="abs display footer-title" style="left:399px;top:1960px">Information</h4>
  <ul class="abs footer-links" style="left:399px;top:2000px">
    <li>Home</li><li>What we do</li><li>How we do it</li><li>Who are we</li><li>Why use us</li><li>Clients</li><li>Partners</li><li>Contact</li>
  </ul>

  <h4 class="abs display footer-title" style="left:590px;top:1960px">Newsletter Subscription</h4>
  <p class="abs footer-links" style="left:590px;top:2002px;width:230px">Register your Email Address to get Information about us</p>
  <div class="abs email-field">Email Address</div>
  <div class="abs outline-btn" style="left:590px;top:2114px;width:95px;height:30px;line-height:28px;font-weight:400">SUBSCRIBE</div>

  <h4 class="abs display footer-title" style="left:915px;top:1960px">Contact Us</h4>
  <div class="abs contact-row" style="left:915px;top:2003px">
    <svg width="10" height="14" viewBox="0 0 10 14" style="margin-top:3px"><path d="M5 0a5 5 0 0 1 5 5c0 4-5 9-5 9S0 9 0 5a5 5 0 0 1 5-5z" fill="var(--red)"/><circle cx="5" cy="5" r="2" fill="#fff"/></svg>
    <span>Suite 4 Larkfield Court,<br>Oldbrook, Fenwick,<br>Hants, FW12 3PQ</span>
  </div>
  <div class="abs contact-row" style="left:915px;top:2086px">
    <svg width="12" height="12" viewBox="0 0 12 12" style="margin-top:4px"><path d="M2 0h3l1 3-2 1.5a7 7 0 0 0 3.5 3.5L9 6l3 1v3a2 2 0 0 1-2 2A10 10 0 0 1 0 2a2 2 0 0 1 2-2z" fill="var(--red)"/></svg>
    <span>+1-555-014-2770</span>
  </div>
  <div class="abs contact-row" style="left:915px;top:2127px">
    <svg width="13" height="10" viewBox="0 0 13 10" style="margin-top:5px"><rect width="13" height="10" fill="var(--red)"/><path d="M0 0l6.5 5L13 0" fill="none" stroke="#fff" stroke-width="1.2"/></svg>
    <span>info@brightmoor-counsel.com</span>
  </div>

  <div class="abs footer-divider"></div>
  <p class="abs copyright">Copyrights © 2017, Brightmoor Counsel. All rights reserved.</p>
  <div class="abs socials"><span></span><span></span><span></span><span></span></div>
</footer>

</body>
</html>
```